AMberleaf Tasting Society Business Card design

Create a new business card that is contemporary but maintains the air of wine and the logo's history. I have put the original logo and a more current logo. The element we would like to keep intact is the visual the two gentleman holding the wine glasses...however, if there is an interesting interpretation of these two figures, have at it.

the company name is:

The Amberleaf Tasting Society
478 E. Larkspur Rd.
Cedarvale, CA 90471
800-555-0172

```html
<!DOCTYPE html>
<html lang="en">
<head>
<meta charset="utf-8">
<title>Amberleaf Tasting Society Business Card</title>
<link href="https://fonts.googleapis.com/css2?family=IM+Fell+English:ital@0;1&family=Montserrat:wght@500&display=swap" rel="stylesheet">
<style>
  :root {
    --wine: #8f1a35;
    --paper: #ffffff;
    --backdrop: #d9d9d9;
  }
  html, body {
    margin: 0;
    padding: 0;
    width: 1200px;
    height: 800px;
    overflow: hidden;
    background: var(--backdrop);
  }
  .sheet {
    position: relative;
    width: 1200px;
    height: 800px;
    display: flex;
    justify-content: center;
    align-items: center;
    gap: 80px;
  }
  .card {
    position: relative;
    width: 330px;
    height: 570px;
    box-shadow: 0 6px 18px rgba(0,0,0,0.18);
  }
  .card-frame {
    position: absolute;
    inset: 0;
    display: block;
  }
  .card-content {
    position: absolute;
    inset: 0;
    display: flex;
    flex-direction: column;
    align-items: center;
    justify-content: center;
    text-align: center;
    color: var(--wine);
  }
  .brand-name {
    font-family: "IM Fell English", serif;
    font-size: 30px;
    line-height: 1.05;
    margin: 0;
  }
  .brand-phone {
    font-family: "Montserrat", sans-serif;
    font-weight: 500;
    font-size: 11px;
    letter-spacing: 0.5px;
    margin: 8px 0 44px;
  }
  .person-name {
    font-family: "IM Fell English", serif;
    font-style: italic;
    font-size: 26px;
    margin: 0;
    line-height: 1;
  }
  .person-title {
    font-family: "Montserrat", sans-serif;
    font-weight: 500;
    font-size: 14px;
    margin: 4px 0 48px;
  }
  .contact {
    font-family: "Montserrat", sans-serif;
    font-weight: 500;
    font-size: 15px;
    line-height: 1.35;
    margin: 0;
  }
  .contact-phone {
    margin-top: 14px;
  }
</style>
</head>
<body>
<main class="sheet">

  <section class="card card-front">
    <svg class="card-frame" width="330" height="570" viewBox="0 0 330 570">
      <rect width="330" height="570" fill="var(--wine)" role="img" aria-label="Ornamental vine and leaf border pattern"/>
      <ellipse cx="165" cy="285" rx="158" ry="272" fill="var(--paper)"/>
    </svg>
    <div class="card-content">
      <p class="brand-name">Amberleaf<br>Tasting Society</p>
      <p class="brand-phone">626-555-0148</p>
      <p class="person-name">Daniel Reyes</p>
      <p class="person-title">Founder</p>
      <p class="contact">478 E. Larkspur Rd.<br>Cedarvale, CA 90471</p>
      <p class="contact contact-phone">800-555-0172</p>
    </div>
  </section>

  <section class="card card-back">
    <svg class="card-frame" width="330" height="570" viewBox="0 0 330 570">
      <rect width="330" height="570" fill="var(--wine)" role="img" aria-label="Ornamental vine and leaf border pattern"/>
      <ellipse cx="165" cy="285" rx="158" ry="272" fill="var(--paper)"/>
      <rect x="95" y="150" width="140" height="270" rx="30" fill="var(--wine)" role="img" aria-label="Engraved illustration of two gentlemen in period dress holding wine glasses"/>
    </svg>
  </section>

</main>
</body>
</html>
```